Trade Show Design

Two, doublesided backdrops/one doublesided banner/one countertop. I have 3 sample pictures of the 3 items that we are purchasing and all the dimensions are listed on the file names.
website: www.brickwisestudio.net
We are a training center that teaches homeowner's how to do their own home renovations through in-person classes with hands-on training.
We are looking to update our tradeshow displays utilizing stock photos as our photos do not have high enough resolution. I have attached lots of example pictures to select from but some of my favourites that I want to use are over 10 MB so they won't upload. Will have to figure out a different way to upload. Our tagline is Build the skills, own the project. We also use words such as "learn to reno" or "practical, hands-on training". We want to use our current branding (pictures of our minivan are uploaded as well) and our color palette document and really show people what we are all about - classes that people can attend so they can learn to reno their home.
Updates

For the 2 backdrops, we would like them to either be stand-alone or together incase we go to a trade show and only have room for 1 of them. They are to be different designs, front and back but a continuous flow if we are to use them together. Again, I have to figure out how to upload additional pictures as some of the ones I want to use are larger. Thanks!

Same with the Banner that is also double-sided - this is to be a different design for the back and front. We want minimal wording on everything but we really want to showcase what we do so that people can figure it out quickly when they walk by our booth....we offer in-person class with hands-on training. Learn to do by doing. Like on our vehicle that I sent example pictures of, we can put a list of a few topics so that people can understand:
Renovation Topics:
Bathroom
Drywall
Flooring
Tiling
Basement
Framing
Plumbing
Baseboards
Feature Walls

Here is the link to the Vornel Box to additional photos.

https://files.vornelbox.net/shared/7QK4r_mz2-TX8LwBnPe5YuJsdA0fGhRkZ?view=open

Thanks,
Marla

```html
<!DOCTYPE html>
<html lang="en">
<head>
<meta charset="utf-8">
<title>Brickwise Studio – Roll-up Banners</title>
<link rel="stylesheet" href="https://fonts.googleapis.com/css2?family=Anton&family=Figtree:wght@500;800&display=swap">
<style>
  :root{
    --stage:#b9b9b9;
    --sheet:#f3f3f3;
    --teal:#114b55;
    --blue:#7f9cc4;
    --blue-pale:#c6d5e8;
    --olive:#85826f;
    --gold:#e6cf8f;
    --orange:#d88a1c;
    --sand:#d6d5c0;
  }
  *{box-sizing:border-box;margin:0;padding:0}
  html,body{width:886px;height:1200px;overflow:hidden;background:var(--stage)}
  .stage{position:relative;width:886px;height:1200px}
  .banner{position:absolute;top:40px;width:400px;height:1120px;background:var(--sheet);overflow:hidden}
  .banner--left{left:30px}
  .banner--right{left:456px}
  .deco{position:absolute;left:0;top:0}
  .photo{position:absolute}
  .brand{position:absolute;left:0;width:100%;text-align:center;font-family:"Figtree",sans-serif;color:var(--teal)}
  .brand__name{display:inline-flex;align-items:center;gap:8px;font-weight:800;font-size:24px;letter-spacing:.5px}
  .brand__mark{width:16px;height:16px;background:var(--orange)}
  .brand__tag{font-weight:500;font-size:12px;margin-top:4px}
  .headline{position:absolute;font-family:"Anton",sans-serif;line-height:1;white-space:nowrap}
  .headline--learn{left:92px;top:752px;font-size:74px;color:var(--teal)}
  .headline--to{left:268px;top:776px;font-size:58px;color:var(--blue)}
  .headline--reno{left:186px;top:828px;font-size:82px;color:var(--olive)}
  .offer{position:absolute;left:0;width:100%;text-align:center;font-family:"Anton",sans-serif;line-height:1;white-space:nowrap}
  .offer__intro{top:230px;font-size:30px;color:var(--olive)}
  .offer__box{top:268px;left:95px;width:210px;height:60px;background:var(--teal);color:#fff;font-size:42px;display:flex;align-items:center;justify-content:center}
  .offer__classes{top:340px;font-size:38px;color:var(--blue)}
  .offer__hands{top:386px;font-size:32px;color:var(--teal)}
  .topic{position:absolute;left:0;width:100%;text-align:center;font-family:"Figtree",sans-serif;font-weight:800;font-size:13px;line-height:1.55}
  .topic svg{display:block;margin:0 auto 10px}
  .topic--teal{color:var(--teal)}
  .topic--olive{color:var(--olive)}
</style>
</head>
<body>
<main class="stage">

  <section class="banner banner--left">
    <svg class="deco" width="400" height="1120" viewBox="0 0 400 1120">
      <rect x="66" y="32" width="292" height="378" fill="var(--blue-pale)"/>
      <rect x="46" y="394" width="40" height="20" fill="var(--blue-pale)"/>
      <polygon points="100,300 302,356 302,610 100,610" fill="var(--gold)" transform="translate(10,0)"/>
      <polygon points="62,740 94,726 94,852 180,852 180,868 62,868" fill="var(--blue)"/>
      <path d="M144 922 Q200 914 236 918 Q246 926 258 920 Q290 922 320 924" stroke="var(--orange)" stroke-width="2.5" fill="none"/>
      <rect x="290" y="940" width="70" height="180" fill="#b7d3d4"/>
    </svg>
    <div class="photo" role="img" aria-label="Photo: woman in safety glasses driving a screw into drywall with a cordless drill"
         style="left:52px;top:20px;width:292px;height:378px;background:linear-gradient(160deg,#e4dccb,#c9bba0 60%,#6d8fa8)"></div>
    <div class="photo" role="img" aria-label="Photo: smiling woman holding two cordless drills"
         style="left:96px;top:330px;width:196px;height:270px;clip-path:polygon(0 0,100% 55px,100% 100%,0 100%);background:linear-gradient(180deg,#efece6,#d8cbb6 60%,#4f6f9e)"></div>
    <div class="brand" style="top:650px">
      <div class="brand__name"><span class="brand__mark"></span>Brickwise Studio</div>
      <div class="brand__tag">Build the skills, own the project.</div>
    </div>
    <div class="headline headline--learn">Learn</div>
    <div class="headline headline--to">To</div>
    <div class="headline headline--reno">Reno</div>
    <div class="photo" role="img" aria-label="Photo: bearded man in safety glasses fitting a panel in a workshop"
         style="left:52px;top:940px;width:238px;height:180px;background:linear-gradient(120deg,#7a5a36,#c59a62 50%,#5b6a72)"></div>
  </section>

  <section class="banner banner--right">
    <svg class="deco" width="400" height="1120" viewBox="0 0 400 1120">
      <polygon points="286,36 358,44 358,132 286,84" fill="var(--sand)"/>
      <polygon points="0,800 16,800 16,888 84,888 84,916 0,918" fill="var(--blue)"/>
      <polygon points="70,930 352,880 352,894 70,944" fill="var(--gold)"/>
    </svg>
    <div class="brand" style="top:100px">
      <div class="brand__name"><span class="brand__mark"></span>Brickwise Studio</div>
      <div class="brand__tag">Build the skills, own the project.</div>
    </div>
    <div class="offer offer__intro">We Offer</div>
    <div class="offer offer__box">IN-PERSON</div>
    <div class="offer offer__classes">CLASSES WITH</div>
    <div class="offer offer__hands">Hands-On Training</div>

    <div class="topic topic--teal" style="top:470px">
      <svg width="40" height="44" viewBox="0 0 40 44" fill="none" stroke="var(--teal)" stroke-width="3">
        <path d="M6 44V12a8 8 0 0 1 16 0"/><path d="M14 16h18l-4 6H18z" fill="var(--teal)"/>
        <path d="M18 28l-2 6M24 28v7M30 28l2 6M21 38l-1 4M28 38l1 4" stroke-width="2"/>
      </svg>
      TILING &nbsp;|&nbsp; BATHROOM<br>PLUMBING
    </div>
    <div class="topic topic--olive" style="top:600px">
      <svg width="44" height="44" viewBox="0 0 44 44" fill="var(--olive)">
        <rect x="6" y="4" width="24" height="12" rx="3"/><rect x="30" y="8" width="10" height="4"/>
        <rect x="12" y="16" width="10" height="16"/><rect x="8" y="32" width="18" height="10" rx="2"/>
      </svg>
      DRYWALL &nbsp;|&nbsp; FRAMING<br>FEATURE WALLS
    </div>
    <div class="topic topic--teal" style="top:740px">
      <svg width="46" height="50" viewBox="0 0 46 50" fill="var(--teal)">
        <rect x="4" y="24" width="38" height="24" rx="3"/><rect x="10" y="4" width="6" height="22"/>
        <rect x="22" y="8" width="6" height="18"/><circle cx="34" cy="8" r="6"/><rect x="32" y="12" width="4" height="14"/>
        <rect x="14" y="34" width="18" height="4" fill="var(--sheet)"/>
      </svg>
      FLOORING &nbsp;|&nbsp; BASEMENT<br>BASEBOARDS
    </div>

    <div class="photo" role="img" aria-label="Photo: young woman in work gloves measuring a wooden board with a tape measure"
         style="left:70px;top:892px;width:282px;height:228px;clip-path:polygon(0 52px,100% 0,100% 100%,0 100%);background:linear-gradient(130deg,#6a4a32,#b58a62 45%,#e8d9c0 75%,#7b93b0)"></div>
  </section>

</main>
</body>
</html>
```